Simple landing page for Brambles cookbook

I need a one page landingpage where customers can order the cookbook.
This is a cookbook of a collection of recipes from our deli that we used to run.
I need a landing page where customers can come and order the book. I also need it coded. I already have the domain through hostwell.
I can send the file of the book through wetransfer. It's too big to upload here. Just so you get the feel that I am looking for.
I attached a simple text as an introduction to the page. But I am open to any suggestions. I want it all to be about the experience that we are sharing the recipes with everybody and that it's for sale. The book is $29.99, shipping included.
Customers have to be able to click and buy the book from it.

Coding

Coded - Design and coding required

Number of Pages Required

1 page

Font styles to use
Sans Serif

Requirements
Must have
• Same colors as the cookbook

```html
<!DOCTYPE html>
<html lang="en">
<head>
<meta charset="utf-8">
<title>Brambles Sandwiches – Cookbook</title>
<link href="https://fonts.googleapis.com/css2?family=Domine:wght@700&family=Poppins:wght@400;500;600;700&display=swap" rel="stylesheet">
<style>
  :root {
    --brown-deep: #3d2314;
    --brown-photo: #4a2c1c;
    --brown-dark: #24140c;
    --berry: #d81b5a;
    --ink: #2a2a2a;
    --paper: #ffffff;
    --blush: #fbeeee;
    --cover-sky: #dfeef8;
    --cover-white: #f7fbfe;
  }
  * { box-sizing: border-box; margin: 0; padding: 0; }
  html, body { width: 1200px; height: 643px; overflow: hidden; background: var(--paper); }
  .landing {
    position: relative;
    width: 1200px;
    height: 643px;
    overflow: hidden;
    font-family: "Poppins", sans-serif;
    color: var(--ink);
  }
  .landing__backdrop {
    position: absolute; inset: 0;
    background:
      radial-gradient(circle at 62% 20%, rgba(230,120,120,0.16), transparent 28%),
      radial-gradient(circle at 92% 70%, rgba(230,120,120,0.12), transparent 30%),
      radial-gradient(circle at 70% 85%, rgba(230,120,120,0.10), transparent 25%),
      linear-gradient(90deg, var(--blush), var(--paper) 70%);
  }
  .hero-photo { position: absolute; left: 0; top: 0; }
  .book-cover {
    position: absolute;
    left: 90px; top: 51px;
    width: 313px; height: 549px;
    border-radius: 4px 2px 2px 4px;
    background: linear-gradient(180deg, var(--cover-white) 0%, var(--cover-sky) 35%, #c79a62 60%, #b8b8b8 100%);
    box-shadow: 10px 10px 24px rgba(0,0,0,0.45);
  }
  .social {
    position: absolute; left: 14px; top: 279px; width: 54px;
    display: flex; flex-direction: column; align-items: center; gap: 18px;
    list-style: none;
  }
  .social__link {
    display: block;
    font-family: "Poppins", sans-serif; font-weight: 500;
    font-size: 10px; line-height: 16px;
    color: var(--paper); text-decoration: none;
  }
  .brand {
    position: absolute; right: 53px; top: 30px;
  }
  .brand__name {
    font-family: "Poppins", sans-serif; font-weight: 700;
    font-size: 33px; line-height: 1; letter-spacing: 0.5px;
    color: var(--brown-deep);
  }
  .intro {
    position: absolute; right: 53px; top: 150px; width: 580px;
    text-align: right;
  }
  .intro__title {
    font-family: "Domine", serif; font-weight: 700;
    font-size: 34px; letter-spacing: 1px;
    color: var(--brown-deep); line-height: 1.2;
  }
  .intro__text {
    margin-top: 22px;
    font-size: 11.3px; line-height: 28.3px;
    color: var(--ink);
  }
  .intro__line { display: block; white-space: nowrap; }
  .order {
    position: absolute; right: 54px; top: 502px;
    display: flex; align-items: center; gap: 32px;
  }
  .order__price {
    font-family: "Domine", serif; font-weight: 700;
    font-size: 38px; color: var(--berry);
  }
  .order__button {
    display: flex; align-items: center; justify-content: center;
    width: 231px; height: 49px; border-radius: 25px;
    background: var(--brown-deep); color: var(--paper);
    font-family: "Poppins", sans-serif; font-weight: 500; font-size: 18px;
    text-decoration: none;
    box-shadow: 0 3px 8px rgba(0,0,0,0.2);
  }
</style>
</head>
<body>
<main class="landing">
  <div class="landing__backdrop" role="img" aria-label="Soft faded photo of fresh tomatoes and herbs"></div>

  <svg class="hero-photo" width="1200" height="643" viewBox="0 0 1200 643">
    <defs>
      <radialGradient id="photoTone" cx="0.3" cy="0.5" r="0.8">
        <stop offset="0" stop-color="#6b3f26"/>
        <stop offset="0.6" stop-color="#4a2c1c"/>
        <stop offset="1" stop-color="#24140c"/>
      </radialGradient>
    </defs>
    <circle cx="153" cy="321.5" r="387" fill="url(#photoTone)" role="img" aria-label="Dimmed photo of a grilled sandwich on a checkered cloth"/>
  </svg>

  <div class="book-cover" role="img" aria-label="Cookbook cover: Your ultimate guide to creating your own favourite Brambles sandwiches, 28 delicious recipes"></div>

  <ul class="social" aria-label="Social links">
    <li><a class="social__link" href="#">Facet</a></li>
    <li><a class="social__link" href="#">Chirp</a></li>
    <li><a class="social__link" href="#">Lens</a></li>
  </ul>

  <div class="brand">
    <span class="brand__name">BRAMBLES</span>
  </div>

  <section class="intro">
    <h1 class="intro__title">INTRODUCTION</h1>
    <p class="intro__text">
      <span class="intro__line">Opening it’s doors in January of 2010, Brambles European Deli was a sandwich shop in Millbrook,</span>
      <span class="intro__line">New Brunswick, but also a lot more than that. We spent five years with this business closure in</span>
      <span class="intro__line">April of 2015. It was a special time where we met tons of amazing people, who we loved to see</span>
      <span class="intro__line">and serve.Brambles started out as a deli but eventually morphed into the sandwich shop we all</span>
      <span class="intro__line">know it as today.&nbsp; We are overwhelmed with the continuous positive&nbsp; comments we geton our</span>
      <span class="intro__line">that is still up and running. Unfortunately, we can’t open another Brambles, but we can offer you</span>
      <span class="intro__line">this collection of our recipes for you to try out at home with your family and friends. We truly</span>
      <span class="intro__line">hope you will enjoy making these sandwiches just as much as we did.&nbsp; If you do, please post</span>
      <span class="intro__line">your pictures of you making a meal or the finished product, or even enjoying it!</span>
    </p>
  </section>

  <div class="order">
    <span class="order__price">$29.99</span>
    <a class="order__button" href="#">Book Now</a>
  </div>
</main>
</body>
</html>
```